Bold, Modern, Clean "Kestrelwaymassage.com" website

Why we stand out?
We are a male and female mobile massage team. Our names are Paul and Lina. 
Kestrel Way is a Seattle based mobile massage service. Our massage is offered to the community with a goal of facilitating balance within each individual. We specialize in integrated Pain management, and sports/medical massage therapy. Every client's first assessment is attended by our male and female massage therapist team. Depending on the goals identified for an individual determines which therapist will be assigned to provide treatment, if not both.

Our passion...
Here at Kestrel Way, we have a great passion for Postural Resoration and how it is integrated into an individual's Massage treatment. We pride ourselves in being natural facilitators of healing, which takes the ego of the therapist out of the client's healing process. We strive to deliver the best massage possible by including modalities such as Neuromuscular, Myofascial release, spontaneous muscle release, postural restoration, orthopedic, and medical massage.

Our education...

We are both Graduates of Venmora, school of massage therapy. We have continuing education in medical massage, myofacial release, trigger point therapy, postural restoration, anatomy, and spontaneous muscle release. Lina is also a Certified Yoga Instructor, which amplifies her experience with flexibility and strength as it pertains to each individual. Paul's passion is Massage, stretching, and strength training to encourage postural restoration and realignment.

Our rates-

Our rates are $75/ 60 minutes, $95/ 90 minutes, and $120/ 120 minutes.

Education-
Both Lina and I worked as behavioral health professionals that specialized in life skills mentoring for youth who had experienced different types of trauma. This led us both to want to help others in a different environment, where individuals can be empowered to take responsibility over their own healing. To us, massage is a type of manipulation physical therapy, that encourages healing on many levels.

Advice to any massage client-
The most important thing to 'us', as Licenced providers is to get you on to our table to show you our skills. But a good therapist never forgets that it's not about what we do for you, but what we can facilitate for you. Your health and healing has nothing to do with us. It is yours, not ours. Identify what your goals are with any Therapist, and know what the end looks like. Progress should be tangible, such as range of motion, and decreased pain.

Lina and Paul at Kestrel Way are awesome! I recently had open heart surgery, and Lina worked on me to increase my range of motion while helping with the pinched nerve from my arm being in the same position for so long during my surgery. My wife drives a lot for work, and Paul has helped decrease her neck and lower back pain immensely. They are seriously the best therapists I have ever worked with. I would recommend them to anyone who needs anything from stress relief to a medical massage treatment. They are professional, up beat, easy going, and always on time. And, I love that they meet us where ever we like! We did a staycation recently, where they came to our hotel to give us relaxation massages. Although usually they come to our home, where we focus on pain related issues. We will continue to work with them for a long, long time.

Target Market(s)

Mobile massage therapy clients

Industry/Entity Type

Massage Therapy

Coding

Coded - Design and coding required

Number of Pages Required

1 page

Font styles to use
Serif
Sans Serif

Requirements
Must have
• Please add or remove any information that would help the presentation of our website. Our logo is posted below, please include into the website.
• Please include a contact field that includes, kestrelwaymassage@fernmail.net,
• (206) 555-0148
• We have also included our own stock photos, as well as a photo of Paul and Lina. Please include a cropped photo of both massage therapists.

```html
<!DOCTYPE html>
<html lang="en">
<head>
<meta charset="utf-8">
<title>Kestrel Way Mobile Massage</title>
<link rel="stylesheet" href="https://fonts.googleapis.com/css2?family=Lato:wght@300;400;700&family=Oswald:wght@400&family=Raleway:wght@300;400&display=swap">
<style>
:root{
  --black:#0b0b0b;
  --ink:#222;
  --teal:#1fc4b4;
  --teal-deep:#0f9f94;
  --teal-dark:#0a5d57;
  --navy:#0d1f9a;
  --blue:#1a56c4;
  --grey-bg:#f2f2f2;
  --dark:#1c1c1c;
  --white:#fff;
  --muted:#555;
}
*{box-sizing:border-box;margin:0;padding:0}
html,body{width:1200px;height:3041px;overflow:hidden}
body{font-family:'Lato',sans-serif;color:var(--ink);background:var(--white);position:relative}
.abs{position:absolute}
/* header */
.topbar{position:absolute;left:0;top:0;width:1200px;height:97px;background:var(--black)}
.contact-line{position:absolute;top:36px;color:var(--white);font-size:15px;display:flex;align-items:center;gap:10px}
.contact-line .dot{width:26px;height:26px;border-radius:50%;background:var(--navy);display:flex;align-items:center;justify-content:center}
.navbar{position:absolute;left:0;top:97px;width:1200px;height:45px;background:linear-gradient(var(--teal),var(--teal-deep))}
.nav-item{position:absolute;top:0;height:45px;line-height:45px;color:var(--white);font-size:14px;font-weight:700;letter-spacing:.3px;transform:translateX(-50%);white-space:nowrap}
.nav-item.active{background:var(--black);width:98px;text-align:center;transform:none}
.brand{position:absolute;left:60px;top:20px;width:193px;height:193px;border-radius:50%;background:var(--navy);border:6px solid var(--white);display:flex;flex-direction:column;align-items:center;justify-content:center;z-index:5;color:var(--white);text-align:center;font-family:'Lato',sans-serif;font-weight:700}
.brand .name{font-size:34px;line-height:1.05}
.brand .sub{font-size:16px;margin-top:6px}
/* hero */
.hero{position:absolute;left:0;top:142px;width:1200px;height:541px;background:linear-gradient(110deg,#c98e6a 0%,#e9c3a6 35%,#d7a583 60%,#efe3d6 100%)}
.hero-caption{position:absolute;left:101px;top:338px;width:588px;height:183px;background:rgba(30,30,30,.78);border-radius:4px;padding:20px 20px;font-family:'Oswald',sans-serif;color:var(--white);font-size:27px;line-height:1.3}
.dots{position:absolute;left:20px;bottom:16px;display:flex;gap:6px}
.dots span{width:11px;height:11px;border-radius:50%;background:#ccc}
.dots span.on{background:var(--teal)}
.van{position:absolute;left:679px;top:365px;width:355px;height:162px;border-radius:40px 70px 14px 14px;background:linear-gradient(#d9dadc,#8d9095)}
/* welcome */
.welcome{position:absolute;left:0;top:683px;width:1200px;height:525px;background:var(--white)}
.h-section{font-family:'Raleway',sans-serif;font-weight:300;font-size:30px;color:#333;display:flex;align-items:center;gap:12px}
.card-photo{position:absolute;top:122px;width:298px;height:154px;border:1px solid #ddd}
.card-title{position:absolute;top:300px;width:298px;text-align:center;font-family:'Raleway',sans-serif;font-size:20px;color:var(--blue)}
.card-text{position:absolute;top:340px;width:298px;text-align:center;font-size:12.5px;line-height:1.75;color:#333}
.btn{position:absolute;width:115px;height:36px;background:var(--navy);color:var(--white);font-size:13px;font-weight:700;text-align:center;line-height:36px;box-shadow:0 3px 4px rgba(0,0,0,.3)}
.booking{position:absolute;left:793px;top:57px;width:308px;height:405px;border:1px solid #ddd;box-shadow:0 4px 8px rgba(0,0,0,.12);background:var(--white);padding:18px 18px}
.booking h3{font-family:'Raleway',sans-serif;font-weight:400;font-size:21px;color:#444;display:flex;gap:8px;align-items:center;margin-bottom:14px}
.field{display:flex;height:44px;margin-bottom:7px}
.field .ic{width:32px;display:flex;align-items:center;justify-content:center;color:#444;font-size:13px}
.field .box{flex:1;border:1px dashed #ccc;font-size:11px;color:#444;padding:14px 10px}
.field.tall{height:122px}
.field.tall .box{padding-top:12px}
/* services */
.services{position:absolute;left:0;top:1208px;width:1200px;height:454px;background:var(--dark)}
.services .h-section,.advice .h-section{color:var(--white);justify-content:center}
.svc{position:absolute;top:120px;width:190px;height:190px;border-radius:50%;border:6px solid var(--teal);background:radial-gradient(circle at 40% 35%,#3fd9d2,#0aa7b3 60%,#08707a);box-shadow:0 10px 18px rgba(0,0,0,.6)}
.svc-label{position:absolute;top:350px;width:300px;text-align:center;color:#eee;font-family:'Raleway',sans-serif;font-size:21px;line-height:1.3}
/* advice */
.advice{position:absolute;left:0;top:1662px;width:1200px;height:355px;background:linear-gradient(100deg,#5a3a2c 0%,#8c5e48 45%,#c89a7e 75%,#6e4a3a 100%)}
.advice .shade{position:absolute;inset:0;background:rgba(40,30,25,.45)}
.badge-circle{position:absolute;width:90px;height:90px;border-radius:50%;border:3px solid var(--white);background:rgba(255,255,255,.15);display:flex;align-items:center;justify-content:center}
.advice h2{position:absolute;top:134px;width:1200px;text-align:center;font-family:'Raleway',sans-serif;font-weight:400;font-size:31px;color:var(--white)}
.advice p{position:absolute;left:110px;top:198px;width:980px;text-align:center;color:var(--white);font-size:13.5px;line-height:1.75}
/* testimonials */
.testimonials{position:absolute;left:0;top:2017px;width:1200px;height:375px;background:var(--grey-bg)}
.testimonials .h-section{justify-content:center}
.quote{position:absolute;font-family:Georgia,serif;font-size:180px;color:#d0d0d0;line-height:1}
.testimonials p{position:absolute;left:130px;top:118px;width:940px;text-align:center;font-size:13.5px;line-height:1.75;color:#222}
.stars{position:absolute;top:262px;width:1200px;text-align:center;font-size:13px;font-weight:700}
.review-badge{position:absolute;left:555px;top:300px;width:90px;height:30px;border-radius:15px;border:2px solid #8a6a2a;background:#f3e3b5}
/* rates */
.rates{position:absolute;left:0;top:2392px;width:1200px;height:446px;background:linear-gradient(#13c6a6,#1ad7b2 40%,#17c3a2)}
.rates h2{position:absolute;top:148px;width:1200px;text-align:center;font-family:'Raleway',sans-serif;font-weight:400;font-size:30px;color:var(--white)}
.rates .lead{position:absolute;top:196px;width:1200px;text-align:center;font-size:14px;color:var(--white)}
.rate-bar{position:absolute;left:122px;top:241px;width:956px;height:45px;border-radius:23px;background:var(--teal-dark);display:flex;color:var(--white);font-size:14px;font-weight:700}
.rate{flex:1;display:flex;align-items:center;justify-content:center;gap:38px;border-right:1px solid rgba(255,255,255,.25)}
.rate:last-child{border-right:none}
.rate span{display:flex;gap:8px;align-items:center}
.foot-brand{position:absolute;left:162px;top:2733px;width:183px;height:183px;border-radius:50%;background:#e8e8e8;border:5px solid #bbb;display:flex;flex-direction:column;align-items:center;justify-content:center;color:#333;font-weight:700;z-index:3}
.foot-brand .name{font-size:31px;line-height:1.05;text-align:center}
.foot-brand .sub{font-size:15px;margin-top:5px}
/* footer */
.footer{position:absolute;left:0;top:2838px;width:1200px;height:158px;background:var(--dark)}
.foot-nav{position:absolute;top:100px;left:0;width:1200px;height:20px}
.foot-nav span{position:absolute;transform:translateX(-50%);color:var(--white);font-size:14px;white-space:nowrap}
.foot-nav i{position:absolute;top:2px;width:1px;height:16px;background:#777}
.bottombar{position:absolute;left:0;top:2996px;width:1200px;height:45px;background:var(--teal);color:#073c37;font-size:12.5px;display:flex;align-items:center;padding-left:100px}
.social{position:absolute;right:100px;top:14px;display:flex;gap:12px}
.social span{width:17px;height:17px;border-radius:50%;background:#073c37}
</style>
</head>
<body>

<header>
  <div class="topbar">
    <div class="contact-line" style="left:708px">
      <span class="dot"><svg width="14" height="14" viewBox="0 0 24 24"><path fill="#fff" d="M6.6 10.8c1.4 2.8 3.8 5.1 6.6 6.6l2.2-2.2c.3-.3.7-.4 1-.2 1.1.4 2.3.6 3.6.6.6 0 1 .4 1 1V20c0 .6-.4 1-1 1C10.6 21 3 13.4 3 4c0-.6.4-1 1-1h3.5c.6 0 1 .4 1 1 0 1.3.2 2.5.6 3.6.1.3 0 .7-.2 1z"/></svg></span>
      (206) 555-0148
    </div>
    <div class="contact-line" style="left:870px">
      <span class="dot"><svg width="14" height="12" viewBox="0 0 24 18"><rect x="1" y="1" width="22" height="16" rx="2" fill="none" stroke="#fff" stroke-width="2"/><path d="M1 2l11 8 11-8" fill="none" stroke="#fff" stroke-width="2"/></svg></span>
      kestrelwaymassage@fernmail.net
    </div>
  </div>
  <nav class="navbar">
    <span class="nav-item active" style="left:324px">HOME</span>
    <span class="nav-item" style="left:540px">WHY WE STAND OUT?</span>
    <span class="nav-item" style="left:734px">OUR PASSION</span>
    <span class="nav-item" style="left:894px">EDUCATION</span>
    <span class="nav-item" style="left:1054px">CONTACT US</span>
  </nav>
  <div class="brand"><span class="name">Kestrel<br>Way</span><span class="sub">mobile massage</span></div>
</header>

<section class="hero" role="img" aria-label="Photo of a couple relaxing during a massage">
  <div class="hero-caption">
    We Are A Seattle Based Mobile Massage Service Specialize In Integrated Pain Management, And Sports/medical Massage Therapy.
    <div class="dots"><span></span><span class="on"></span><span></span><span></span></div>
  </div>
  <div class="van" role="img" aria-label="Photo of the silver mobile massage van"></div>
</section>

<section class="welcome">
  <h2 class="h-section abs" style="left:97px;top:50px">
    <svg width="34" height="30" viewBox="0 0 34 30"><circle cx="8" cy="8" r="5" fill="var(--teal)"/><path d="M2 20h30v4H2z" fill="var(--navy)"/><path d="M10 14l14 4v2H10z" fill="var(--teal)"/></svg>
    Welcome to Kestrel Way Mobile Massage
  </h2>
  <div class="card-photo" style="left:111px;background:linear-gradient(120deg,#b7bcc4,#e6d2c4 50%,#caa28a)" role="img" aria-label="Photo of a therapist treating a client with a massage device"></div>
  <h3 class="card-title" style="left:111px">Our Passion</h3>
  <p class="card-text" style="left:111px">Here at Kestrel Way, we have a great passion for Postural Resoration and how it is integrated into an individual's Massage treatment...</p>
  <span class="btn" style="left:202px;top:421px">Read More</span>

  <div class="card-photo" style="left:448px;background:linear-gradient(120deg,#d9b49a,#f0e6dc 50%,#c9a58c)" role="img" aria-label="Photo of therapists Paul and Lina"></div>
  <h3 class="card-title" style="left:448px">Our Education</h3>
  <p class="card-text" style="left:448px">We are both Graduates of Venmora, school of massage therapy. We have continuing education in medical massage, myofacial release...</p>
  <span class="btn" style="left:540px;top:421px">Read More</span>

  <form class="booking">
    <h3><svg width="20" height="20" viewBox="0 0 20 20"><rect x="2" y="3" width="14" height="15" rx="2" fill="none" stroke="var(--teal)" stroke-width="2"/><path d="M8 12l9-9" stroke="var(--teal)" stroke-width="2"/></svg>Book An Appointment</h3>
    <div class="field"><span class="ic">&#9679;</span><span class="box">Name</span></div>
    <div class="field"><span class="ic">&#9993;</span><span class="box">Email</span></div>
    <div class="field"><span class="ic">&#9742;</span><span class="box">Phone</span></div>
    <div class="field tall"><span class="ic">&#9998;</span><span class="box">Message</span></div>
    <span class="btn" style="left:18px;top:355px">Book Now</span>
  </form>
</section>

<section class="services">
  <h2 class="h-section abs" style="left:0;top:45px;width:1200px">
    <svg width="26" height="28" viewBox="0 0 26 28"><circle cx="13" cy="8" r="6" fill="none" stroke="var(--teal)" stroke-width="2.5"/><path d="M3 26c2-8 18-8 20 0" fill="none" stroke="var(--teal)" stroke-width="2.5"/></svg>
    Our Services
  </h2>
  <div class="svc" style="left:205px" role="img" aria-label="Integrated pain management emblem"></div>
  <div class="svc" style="left:505px" role="img" aria-label="Sports massage emblem"></div>
  <div class="svc" style="left:803px" role="img" aria-label="Medical massage emblem"></div>
  <p class="svc-label" style="left:150px">Integrated<br>Pain management</p>
  <p class="svc-label" style="left:450px">Sports<br>Massage Therapy</p>
  <p class="svc-label" style="left:748px">Medical<br>Massage Therapy</p>
</section>

<section class="advice" role="img" aria-label="Photo of a woman resting during a facial massage">
  <div class="shade"></div>
  <div class="badge-circle" style="left:555px;top:26px">
    <svg width="44" height="44" viewBox="0 0 44 44"><circle cx="18" cy="18" r="8" fill="#fff"/><path d="M4 40c2-12 26-12 28 0z" fill="#fff"/><circle cx="32" cy="12" r="8" fill="none" stroke="#fff" stroke-width="2"/><path d="M32 9v6" stroke="#fff" stroke-width="2"/></svg>
  </div>
  <h2>Advice To Any Massage Client</h2>
  <p>The Most Important Thing To 'us', As Licenced Providers Is To Get You On To Our Table To Show You Our Skills, But A Good Therapist Never Forgets That It's Not About What We Do For You, But What We Can Facilitate For You. Your Health And Healing Has Nothing To Do With Us. It Is Yours, Not Ours. Identify What Your Goals Are With Any Therapist, And Know What The End Looks Like. Progress Should Be Tangible, Such As Range Of Motion, And Decreased Pain.</p>
</section>

<section class="testimonials">
  <h2 class="h-section abs" style="left:0;top:50px;width:1200px">
    <svg width="32" height="30" viewBox="0 0 32 30"><circle cx="12" cy="16" r="9" fill="var(--teal)"/><circle cx="25" cy="6" r="4" fill="var(--teal)"/></svg>
    Clients Testimonials
  </h2>
  <span class="quote" style="left:30px;top:118px">&ldquo;</span>
  <span class="quote" style="left:1090px;top:148px">&rdquo;</span>
  <p>Lina and Paul at Kestrel Way are awesome! I recently had open heart surgery, and Lina worked on me to increase my range of motion while helping with the pinched nerve from my arm being in the same position for so long during my surgery. My wife drives a lot for work, and Paul has helped decrease her neck and lower back pain immensely. They are seriously the best therapists I have ever worked with. I would recommend them to anyone who needs anything from stress relief to a medical massage treatment. They are professional, upbeat, easy going, and always on time. And, I love that they meet us where ever we like! We did a staycation recently, where they came to our hotel to give us relaxation massages. Although usually they come to our home, where we focus on pain related issues. We will continue to work with them for a long, long time.</p>
  <div class="stars">5/5 stars Massage Therapy</div>
  <span class="review-badge"></span>
</section>

<section class="rates">
  <div class="badge-circle" style="left:555px;top:40px">
    <svg width="44" height="44" viewBox="0 0 44 44"><circle cx="17" cy="26" r="12" fill="none" stroke="#fff" stroke-width="3"/><text x="17" y="32" text-anchor="middle" fill="#fff" font-family="Lato,sans-serif" font-weight="700" font-size="16">$</text><path d="M26 16c0-8 8-12 14-12 0 8-6 12-14 12z" fill="#fff"/></svg>
  </div>
  <h2>Our Rates</h2>
  <p class="lead">Lorem Ipsum Dolor Sit Amet Ex Vim Quem Primis, Quot Suavitate Mole.</p>
  <div class="rate-bar">
    <div class="rate"><span>&#10148; $ 75 per</span><span>&#9719; 60 minutes</span></div>
    <div class="rate"><span>&#10148; $ 95 per</span><span>&#9719; 90 minutes</span></div>
    <div class="rate"><span>&#10148; $ 120 per</span><span>&#9719; 120 minutes</span></div>
  </div>
  <svg class="abs" style="left:0;top:346px" width="1200" height="100" viewBox="0 0 1200 100" preserveAspectRatio="none">
    <path d="M0 60 C300 100 700 100 1200 0 V100 H0z" fill="#fff" opacity=".9"/>
    <path d="M0 80 C350 110 750 110 1200 30 V100 H0z" fill="var(--dark)"/>
  </svg>
</section>

<div class="foot-brand"><span class="name">Kestrel<br>Way</span><span class="sub">mobile massage</span></div>

<footer class="footer">
  <div class="foot-nav">
    <span style="left:204px">HOME</span><i style="left:254px"></i>
    <span style="left:393px">WHY WE STAND OUT?</span><i style="left:517px"></i>
    <span style="left:603px">OUR PASSION</span><i style="left:703px"></i>
    <span style="left:789px">EDUCATION</span><i style="left:873px"></i>
    <span style="left:970px">CONTACT US</span>
  </div>
</footer>
<div class="bottombar">
  &copy; 2016 KESTREL WAY MOBILE MASSAGE &nbsp;|&nbsp; All Rights Reserved
  <div class="social"><span></span><span></span><span></span></div>
</div>

</body>
</html>
```